Bookkeeping business needs a digital and print flyer

We need a flyer to promote our virtual bookkeeping services to small and mid-sized businesses in the United States. We want the content and design of the flyer to be consistent with our website: www.brightlanebookkeeping.example. We would like both a print version and a digital version of the flyer.

```html
<!DOCTYPE html>
<html lang="en">
<head>
<meta charset="utf-8">
<title>Bright Lane Bookkeeping — Flyer</title>
<link rel="stylesheet" href="https://fonts.googleapis.com/css2?family=Montserrat:wght@400&family=Kanit:ital,wght@1,700;1,800&family=Nunito:wght@400;600;700&family=Nunito+Sans:wght@300;400&display=swap">
<style>
  :root {
    --backdrop: #7cc6ec;
    --ink: #0b0a0c;
    --gold: #f6bd2c;
    --gold-light: #fbd66b;
    --red: #d20b2a;
    --maroon: #7a0d16;
    --white: #ffffff;
  }
  * { box-sizing: border-box; margin: 0; padding: 0; }
  html, body { width: 1200px; height: 800px; overflow: hidden; }
  body { background: var(--backdrop); position: relative; font-family: "Nunito", sans-serif; }

  .flyer {
    position: absolute; left: 332px; top: 20px;
    width: 536px; height: 760px;
    background: var(--gold); overflow: hidden;
  }

  .header { position: absolute; left: 0; top: 0; width: 100%; height: 70px; background: var(--ink); }
  .brand-name {
    position: absolute; left: 36px; top: 24px;
    font-family: "Nunito", sans-serif; font-weight: 600; color: var(--white);
    font-size: 18px; line-height: 22px; white-space: nowrap;
  }

  .call-button {
    position: absolute; left: 298px; top: 18px; width: 195px; height: 34px;
    border-radius: 17px; background: var(--gold); color: var(--ink);
    font-family: "Montserrat", sans-serif; font-size: 13px; font-weight: 400;
    display: flex; align-items: center; justify-content: center; gap: 4px;
  }
  .call-button strong { font-family: "Kanit", sans-serif; font-style: normal; font-weight: 700; text-decoration: underline; }

  .hero-photo {
    position: absolute; left: 0; top: 70px; width: 100%; height: 316px;
    background: linear-gradient(135deg, #b99a79 0%, #6b6660 35%, #2c2f3a 60%, #1a1c22 100%);
  }

  .band-stripes { position: absolute; left: 0; width: 100%; }

  .headline-box {
    position: absolute; left: 260px; top: 265px; width: 255px; height: 218px;
    background: var(--red); border-bottom-left-radius: 38px;
    padding: 18px 6px 0;
    font-family: "Kanit", sans-serif; font-style: italic; font-weight: 800;
    font-size: 20.5px; line-height: 27px; text-align: center; text-transform: uppercase;
    color: var(--ink);
  }
  .headline-box::after {
    content: ""; position: absolute; inset: 4px;
    border: 1px dashed rgba(0,0,0,0.55); border-bottom-left-radius: 34px; pointer-events: none;
  }
  .headline-box .accent { color: var(--gold); }

  .tagline {
    position: absolute; left: 20px; top: 430px;
    font-family: "Kanit", sans-serif; font-style: italic; font-weight: 700;
    font-size: 14.5px; line-height: 18.5px; color: var(--ink); white-space: nowrap;
  }
  .tagline .hero-link { color: var(--maroon); text-decoration: underline; }

  .work-photo {
    position: absolute; left: 0; top: 508px; width: 219px; height: 154px;
    border-top-right-radius: 30px;
    background: linear-gradient(120deg, #c9c2b6 0%, #8e2a2a 45%, #b8231f 60%, #d8d2c8 100%);
  }

  .services { position: absolute; left: 245px; top: 519px; width: 285px; color: var(--ink); }
  .services-title { font-size: 10.5px; font-weight: 600; line-height: 14px; }
  .services-title span { color: var(--maroon); }
  .services-label { font-size: 8.5px; font-weight: 700; color: var(--maroon); text-decoration: underline; margin: 2px 0 6px 0; }
  .service-list { list-style: none; margin-left: -11px; }
  .service-list li { font-size: 7.6px; font-weight: 600; line-height: 9.9px; padding-left: 11px; position: relative; white-space: nowrap; }
  .service-list li::before { content: "☆"; position: absolute; left: 0; top: 0; font-size: 7.5px; }

  .footer { position: absolute; left: 0; top: 689px; width: 100%; height: 71px; background: var(--ink); }
  .contact-icon { position: absolute; top: 677px; width: 38px; height: 38px; border-radius: 50%; background: var(--red); display: flex; align-items: center; justify-content: center; }
  .contact-text { position: absolute; top: 721px; font-family: "Nunito Sans", sans-serif; font-weight: 300; font-size: 12px; color: var(--gold); white-space: nowrap; transform: translateX(-50%); }
</style>
</head>
<body>
  <article class="flyer">
    <header class="header">
      <div class="brand-name">Bright Lane Bookkeeping</div>
      <div class="call-button">CALL NOW <strong>555-014-2290</strong></div>
    </header>

    <div class="hero-photo" role="img" aria-label="Photo of a laptop showing a bookkeeping website beside hands reviewing charts on a clipboard"></div>

    <svg class="band-stripes" style="top:376px" width="536" height="40" viewBox="0 0 536 40" aria-hidden="true">
      <polygon points="0,40 0,10 536,0 536,10" fill="var(--gold)"/>
      <polygon points="0,20 536,4 536,10 0,27" fill="var(--gold-light)"/>
    </svg>

    <div class="headline-box">
      Build<br>Your business by<br><span class="accent">Focusing on what<br>you love,</span><br>Not what drains<br>the life out of<br>you!
    </div>

    <p class="tagline">Take Charge Of Your Business<br>And Concentrate On Your<br>Strengths To <span class="hero-link">Become Its Hero!</span></p>

    <div class="work-photo" role="img" aria-label="Photo of a woman in a red sweater working on paperwork at a laptop"></div>

    <section class="services">
      <h2 class="services-title">Bookkeeping Tailored to <span>YOUR Business Needs</span></h2>
      <p class="services-label">Services Available:</p>
      <ul class="service-list">
        <li>Catch-up and clean-up services</li>
        <li>Transaction importation and categorization</li>
        <li>Monthly reconciliation of all accounts, including assets and loans.</li>
        <li>Monthly financial reports (Balance Sheet, Income Statement, Cash Flow)</li>
        <li>Monthly video conference</li>
        <li>Annual tax-prep package sent to your preparer</li>
        <li>A/R &amp; A/P</li>
        <li>Payroll coordination</li>
        <li>1099s</li>
        <li>Bill pay and receipt management</li>
        <li>Budgeting</li>
      </ul>
    </section>

    <svg class="band-stripes" style="top:664px" width="536" height="26" viewBox="0 0 536 26" aria-hidden="true">
      <polygon points="0,26 0,18 536,0 536,10" fill="var(--gold-light)"/>
    </svg>

    <footer class="footer"></footer>

    <div class="contact-icon" style="left:112px">
      <svg width="20" height="20" viewBox="0 0 24 24" fill="none" stroke="var(--white)" stroke-width="1.6" stroke-linejoin="round" aria-hidden="true">
        <path d="M2 11 L22 3 L16 21 L11 14 Z"/><path d="M11 14 L22 3"/>
      </svg>
    </div>
    <div class="contact-icon" style="left:381px">
      <svg width="20" height="20" viewBox="0 0 24 24" fill="none" stroke="var(--white)" stroke-width="1.6" aria-hidden="true">
        <path d="M12 20 C7 14 5 11 5 8.5 A7 7 0 0 1 19 8.5 C19 11 17 14 12 20 Z"/>
        <circle cx="12" cy="8.5" r="2.5"/>
        <ellipse cx="12" cy="21" rx="6" ry="1.5"/>
      </svg>
    </div>
    <span class="contact-text" style="left:141px">maya@brightlanebookkeeping.example</span>
    <span class="contact-text" style="left:400px">Maple Falls, NE</span>
  </article>
</body>
</html>
```